Velvet Dice Night Age Verification Landing Page

To create a visually appealing design for the landing page of the adult game "Velvet Dice Night" that confirms the visitor's age.
The design should have a simple and visually appealing look that focuses on two buttons labeled "Yes" and "No". The purpose of the page is to confirm that the visitor is 18 years of age or older before accessing the game's content. Responsive design that works well on desktop and mobile devices. The final output should be delivered in PSD, AI, or Sketch format, along with any necessary images or assets.
I have also attached examples.

```html
<!DOCTYPE html>
<html lang="en">
<head>
<meta charset="UTF-8">
<title>Velvet Dice Night — Age Verification</title>
<link href="https://fonts.googleapis.com/css2?family=Barlow:wght@500&family=Inter:wght@400;600;700&display=swap" rel="stylesheet">
<style>
  :root {
    --bg-deep: #1a1c1f;
    --bg-warm: #5a4638;
    --bg-skin: #a2776a;
    --panel: rgba(143, 72, 170, 0.78);
    --panel-edge: #1d1a1f;
    --accent: #b46ad6;
    --accent-soft: #c991e0;
    --text: #ffffff;
    --btn-dark: #1b1b1d;
    --grid-line: rgba(255, 255, 255, 0.05);
  }
  * { margin: 0; padding: 0; box-sizing: border-box; }
  html, body { width: 1200px; height: 609px; overflow: hidden; background: var(--bg-deep); }
  .page {
    position: relative;
    width: 1200px;
    height: 609px;
    overflow: hidden;
    font-family: "Inter", sans-serif;
    color: var(--text);
  }
  .hero-photo {
    position: absolute;
    inset: 0;
    background:
      radial-gradient(ellipse 260px 300px at 640px 240px, rgba(162, 119, 106, 0.55), transparent 70%),
      radial-gradient(ellipse 320px 260px at 950px 420px, rgba(120, 96, 88, 0.45), transparent 70%),
      radial-gradient(ellipse 420px 200px at 300px 580px, rgba(150, 150, 160, 0.25), transparent 70%),
      linear-gradient(120deg, #1e2124 0%, #2a2826 45%, #3b3230 70%, #23252a 100%);
  }
  .grid-overlay {
    position: absolute;
    inset: 0;
    background:
      repeating-linear-gradient(90deg, var(--grid-line) 0 1px, transparent 1px 89px),
      repeating-linear-gradient(0deg, var(--grid-line) 0 1px, transparent 1px 89px);
  }
  .brand {
    position: absolute;
    left: 86px;
    top: 52px;
    display: flex;
    align-items: center;
    gap: 10px;
    font-family: "Inter", sans-serif;
    font-weight: 600;
    font-size: 22px;
    line-height: 1.15;
    color: var(--accent-soft);
    width: 170px;
  }
  .brand-mark {
    flex: none;
    width: 14px;
    height: 14px;
    border-radius: 50%;
    background: var(--accent-soft);
  }
  .music-toggle {
    position: absolute;
    left: 1057px;
    top: 31px;
    width: 57px;
    height: 57px;
    border: 2px solid #ffffff;
    border-radius: 14px;
    background: var(--btn-dark);
    box-shadow: 0 4px 10px rgba(180, 106, 214, 0.6);
    display: flex;
    align-items: center;
    justify-content: center;
  }
  .age-gate {
    position: absolute;
    left: 344px;
    top: 181px;
    width: 513px;
    height: 316px;
    background: var(--panel);
    text-align: center;
  }
  .age-gate-frame {
    position: absolute;
    inset: 0;
    overflow: visible;
  }
  .age-gate-title {
    position: absolute;
    top: 50px;
    left: 0;
    right: 0;
    font-family: "Barlow", sans-serif;
    font-weight: 500;
    font-size: 41px;
    line-height: 48px;
  }
  .title-dots {
    position: absolute;
    top: 107px;
    left: 234px;
    display: flex;
    gap: 3px;
  }
  .title-dots span { width: 7px; height: 7px; background: #ffffff; }
  .age-gate-text {
    position: absolute;
    top: 133px;
    left: 0;
    right: 0;
    font-size: 15px;
    line-height: 27px;
  }
  .age-gate-actions {
    position: absolute;
    top: 214px;
    left: 139px;
    display: flex;
    gap: 18px;
  }
  .btn {
    width: 108px;
    height: 45px;
    display: flex;
    align-items: center;
    justify-content: center;
    gap: 24px;
    font-weight: 700;
    font-size: 15px;
    letter-spacing: 0.5px;
    border-radius: 3px;
    color: var(--text);
  }
  .btn-yes { background: var(--btn-dark); }
  .btn-no { border: 2px solid #ffffff; }
</style>
</head>
<body>
<main class="page">
  <div class="hero-photo" role="img" aria-label="Photograph of a woman lying on a bed in dim bedroom light"></div>
  <div class="grid-overlay"></div>

  <div class="brand"><span class="brand-mark"></span>Velvet Dice Night</div>

  <div class="music-toggle" aria-label="Toggle music">
    <svg width="22" height="22" viewBox="0 0 24 24" fill="none" stroke="#fff" stroke-width="2.2" stroke-linecap="round" stroke-linejoin="round">
      <path d="M9 18V5l11-2v13"/>
      <circle cx="6" cy="18" r="3" fill="#fff"/>
      <circle cx="17" cy="16" r="3" fill="#fff"/>
    </svg>
  </div>

  <section class="age-gate">
    <svg class="age-gate-frame" width="513" height="316" viewBox="0 0 513 316">
      <!-- top edge -->
      <path d="M60 0 L66 5 H134 L140 0 Z" fill="var(--panel-edge)"/>
      <line x1="265" y1="0" x2="345" y2="0" stroke="#fff" stroke-width="1.5" stroke-dasharray="1.5 3" opacity="0.7"/>
      <path d="M370 0 L376 5 H420 L426 0 Z" fill="var(--panel-edge)"/>
      <line x1="372" y1="0" x2="412" y2="0" stroke="var(--accent-soft)" stroke-width="4" stroke-dasharray="4 2"/>
      <!-- left edge -->
      <path d="M0 10 L5 16 V56 L0 62 Z" fill="var(--panel-edge)"/>
      <rect x="-3" y="57" width="3" height="78" fill="var(--accent)"/>
      <line x1="-1" y1="140" x2="-1" y2="172" stroke="var(--accent-soft)" stroke-width="3" stroke-dasharray="3 3"/>
      <path d="M0 222 L5 228 V278 L0 284 Z" fill="var(--panel-edge)"/>
      <!-- right edge -->
      <path d="M513 22 L508 28 V80 L513 86 Z" fill="var(--panel-edge)"/>
      <line x1="510" y1="36" x2="510" y2="74" stroke="#fff" stroke-width="1.5" stroke-dasharray="1.5 3" opacity="0.7"/>
      <rect x="513" y="186" width="3" height="60" fill="var(--accent)"/>
      <path d="M513 246 L508 252 V258 L513 264 Z" fill="var(--panel-edge)"/>
      <!-- bottom edge -->
      <path d="M140 316 L146 311 H300 L306 316 Z" fill="var(--panel-edge)"/>
      <line x1="144" y1="316" x2="178" y2="316" stroke="var(--accent-soft)" stroke-width="4" stroke-dasharray="4 2"/>
      <rect x="178" y="314" width="22" height="4" fill="var(--accent-soft)"/>
      <line x1="210" y1="314" x2="290" y2="314" stroke="#fff" stroke-width="1.5" stroke-dasharray="1.5 3" opacity="0.7"/>
      <path d="M385 316 L391 311 H434 L440 316 Z" fill="var(--panel-edge)"/>
      <line x1="388" y1="316" x2="428" y2="316" stroke="var(--accent-soft)" stroke-width="4" stroke-dasharray="4 2"/>
    </svg>

    <h1 class="age-gate-title">Dirty Games</h1>
    <div class="title-dots"><span></span><span></span><span></span><span></span><span></span></div>
    <p class="age-gate-text">Confirm that the visitor is 18 years of age or<br>older before accessing the game's content.</p>

    <div class="age-gate-actions">
      <div class="btn btn-yes">YES
        <svg width="16" height="14" viewBox="0 0 16 14"><path d="M1.5 7.5 L6 12 L14.5 2" fill="none" stroke="#fff" stroke-width="3" stroke-linecap="round" stroke-linejoin="round"/></svg>
      </div>
      <div class="btn btn-no">NO
        <svg width="11" height="11" viewBox="0 0 11 11"><path d="M1.5 1.5 L9.5 9.5 M9.5 1.5 L1.5 9.5" stroke="#fff" stroke-width="2.6" stroke-linecap="round"/></svg>
      </div>
    </div>
  </section>
</main>
</body>
</html>
```